Business card for Luxury Portable Restroom Trailer company

We are a Luxury Portable Restroom Trailer Company Called FALCRIDGE HIRES. Based in Orange County California. We provide portable restroom trailers for events, such as, Weddings, Concerts, Charity events, Sporting events, Tournaments, Corporate events, ect. We rent and Sell the Luxury restrooms. Our colors are white, grey, and Orange. As you will see in the logo we uploaded.
There are 2 people in the company so the names and titles will change for the 3 people but card will remain the same. Here is the information for each Person: Dwight Penner CFO 555 318-0476
next Person: Leon Marchetti VP 555 318-0476
Next Person: Owen Marchetti CEO 555 318-0476
Information to include on the card: Luxury Restroom Trailers Rental and Sales. Weddings, Concerts, Charity, Sporting and Corp. Events.

```html
<!DOCTYPE html>
<html lang="en">
<head>
<meta charset="utf-8">
<title>Falcridge Hires – Business Card</title>
<link rel="stylesheet" href="https://fonts.googleapis.com/css2?family=Montserrat:wght@400;500;700;800&display=swap">
<style>
  :root {
    --backdrop: #c9c9c9;
    --card: #4f4f51;
    --card-edge: #47474a;
    --orange: #f26b21;
    --white: #ffffff;
    --muted: #e8e8e8;
  }
  * { box-sizing: border-box; margin: 0; padding: 0; }
  html, body {
    width: 1200px; height: 788px; overflow: hidden;
    background: var(--backdrop);
    font-family: "Montserrat", sans-serif;
  }
  .sheet {
    width: 1200px; height: 788px;
    display: flex; align-items: center; justify-content: center; gap: 30px;
  }
  .card {
    position: relative;
    width: 560px; height: 320px;
    background: var(--card);
    overflow: hidden;
    box-shadow: 0 10px 28px rgba(0,0,0,.28);
  }

  /* contact side */
  .corner-mark {
    position: absolute; top: 0; right: 34px;
    width: 26px; height: 26px; background: var(--orange);
  }
  .person { position: absolute; top: 44px; right: 34px; text-align: right; }
  .person-name {
    color: var(--orange); font-weight: 700; font-size: 25px; letter-spacing: 1px;
  }
  .person-title {
    color: var(--white); font-weight: 500; font-size: 13px; letter-spacing: 2px; margin-top: 4px;
  }
  .brand-name {
    position: absolute; top: 44px; left: 34px;
    color: var(--white); font-weight: 800; font-size: 24px; letter-spacing: 1px; line-height: 1.05;
  }
  .contact { position: absolute; left: 34px; bottom: 48px; color: var(--white); font-size: 13px; line-height: 1.45; }
  .contact-address { margin-bottom: 12px; }
  .contact-line { display: flex; align-items: center; gap: 8px; }
  .contact-line svg { width: 12px; height: 12px; fill: var(--orange); flex: none; }
  .edge-band {
    position: absolute; left: 0; right: 0; bottom: 0; height: 12px; display: flex;
  }
  .edge-band .band-orange { flex: 0 0 52%; background: var(--orange); }
  .edge-band .band-white { flex: 1; background: var(--white); }

  /* brand side */
  .card-back {
    display: flex; flex-direction: column; align-items: center; justify-content: center; text-align: center;
  }
  .back-brand { color: var(--white); font-weight: 800; font-size: 44px; letter-spacing: 2px; line-height: 1.05; }
  .back-brand .brand-accent { display: block; font-size: 44px; }
  .tagline { color: var(--orange); font-weight: 500; font-size: 16px; margin-top: 34px; }
  .categories { color: var(--white); font-weight: 500; font-size: 16px; margin-top: 8px; letter-spacing: .3px; }
</style>
</head>
<body>
<main class="sheet">
  <section class="card card-front">
    <div class="corner-mark"></div>
    <div class="brand-name">FALCRIDGE<br>HIRES</div>
    <div class="person">
      <div class="person-name">OWEN MARCHETTI</div>
      <div class="person-title">CEO</div>
    </div>
    <div class="contact">
      <div class="contact-address">4410 Harbor Lane, 3rd Floor<br>Irvine, CA 92614</div>
      <div class="contact-line">
        <svg viewBox="0 0 24 24" aria-hidden="true"><path d="M6.6 10.8a15 15 0 0 0 6.6 6.6l2.2-2.2a1 1 0 0 1 1-.25 11.4 11.4 0 0 0 3.6.57 1 1 0 0 1 1 1V20a1 1 0 0 1-1 1A17 17 0 0 1 3 4a1 1 0 0 1 1-1h3.5a1 1 0 0 1 1 1c0 1.25.2 2.45.57 3.57a1 1 0 0 1-.25 1z"/></svg>
        <span>555 318-0476</span>
      </div>
      <div class="contact-line">
        <svg viewBox="0 0 24 24" aria-hidden="true"><path d="M2 5h20v14H2zm2 2v.5l8 5 8-5V7l-8 5z"/></svg>
        <span>owen@falcridgehires.com</span>
      </div>
      <div class="contact-line">
        <svg viewBox="0 0 24 24" aria-hidden="true"><path d="M12 2a10 10 0 1 0 0 20 10 10 0 0 0 0-20zm0 2c.9 1.1 1.6 2.5 2 4h-4c.4-1.5 1.1-2.9 2-4zM4.3 14a8 8 0 0 1 0-4h3.5a17 17 0 0 0 0 4zm1 2h3c.3 1.3.8 2.5 1.4 3.6A8 8 0 0 1 5.3 16zm3-8h-3a8 8 0 0 1 4.4-3.6C9.1 5.5 8.6 6.7 8.3 8zM12 20c-.9-1.1-1.6-2.5-2-4h4c-.4 1.5-1.1 2.9-2 4zm2.3-6H9.7a15 15 0 0 1 0-4h4.6a15 15 0 0 1 0 4zm.1 5.6c.6-1.1 1.1-2.3 1.4-3.6h3a8 8 0 0 1-4.4 3.6zm1.8-5.6a17 17 0 0 0 0-4h3.5a8 8 0 0 1 0 4z"/></svg>
        <span>www.falcridgehires.com</span>
      </div>
    </div>
    <div class="edge-band"><div class="band-orange"></div><div class="band-white"></div></div>
  </section>

  <section class="card card-back">
    <div class="back-brand">FALCRIDGE<span class="brand-accent">HIRES</span></div>
    <p class="tagline">Luxury Restroom Trailers Rental and Sales</p>
    <p class="categories">Weddings | Concerts | Charity | Sporting | Corp</p>
  </section>
</main>
</body>
</html>
```